Web Design for a Biotech Consulting Firm

We need a web site design for a new business based in Philadelphia called Verantel Dx. This is a consulting firm that will serve medical diagnostics industry, which is part of the life science/healthcare industry focusing on developing and marketing products that help in early detection, monitoring or management of diseases. Our consulting firm will help medical diagnostic companies to overcome key challenges in designing, evaluating and marketing new products.Our company name is Verantel Dx. Verantel is Latin word for "something" Dx represents diagnostics. The idea behind the name is that we help companies to transform the original, early product ideas ("nothing") into "something"; which is a product with full clinical utility that will help to improve health and well-being.The web site should use the visual feel of the logo (attached), be modern, simple and clean looking and represent creativity, innovation, scientific thinking and progress.
Updates

Wix Design is acceptable

Industry/Entity Type

Biotechnology

Coding

Coded - Design and coding required

Number of Pages Required

1 page

Font styles to use
Sans Serif

Requirements
Must have
• simple, clean look couple of pages
Should not have
• a lot of pages

```html
<!DOCTYPE html>
<html lang="en">
<head>
<meta charset="utf-8">
<title>Verantel Dx — Biotech Consulting Firm</title>
<link href="https://fonts.googleapis.com/css2?family=Montserrat:ital,wght@0,400;0,500;0,600;0,700;1,400&display=swap" rel="stylesheet">
<style>
:root{
  --blue:#1a80ec;
  --blue-deep:#0a4fab;
  --ink:#1f2328;
  --muted:#555b63;
  --line:#d7dbe0;
  --panel:#f4f5f7;
  --footer:#2c2e32;
  --footer-bar:#222327;
  --white:#ffffff;
}
*{box-sizing:border-box;margin:0;padding:0}
html,body{width:1200px;height:3143px;overflow:hidden}
body{font-family:"Montserrat",sans-serif;color:var(--ink);background:var(--white)}
.page{position:relative;width:1200px;height:3143px;overflow:hidden}
.abs{position:absolute}
.accent{color:var(--blue)}
.brand{display:flex;align-items:center;gap:10px;font-weight:500;white-space:nowrap}
.brand-square{width:14px;height:14px;background:var(--blue)}

/* header */
.site-header{position:absolute;left:0;top:0;width:1200px;height:106px;background:var(--white)}
.site-header .brand{position:absolute;left:141px;top:38px;font-size:20px;color:var(--ink)}
.contact-chip{position:absolute;top:15px;display:flex;align-items:center;gap:10px}
.chip-icon{width:29px;height:29px;border:1.5px solid var(--blue);display:flex;align-items:center;justify-content:center}
.nav{position:absolute;top:72px;left:0;width:1200px;height:34px}
.nav a{position:absolute;font-size:14px;color:var(--ink);text-decoration:none}
.nav a.active{color:var(--blue)}
.nav a.active::after{content:"";position:absolute;left:-4px;right:-4px;top:30px;height:2px;background:var(--blue)}

/* hero */
.hero{position:absolute;left:0;top:106px;width:1200px;height:494px;background:radial-gradient(circle at 38% 40%,#3f86c8 0,#1f5f9f 40%,#154c86 75%,#0f3c6e 100%)}
.hero-frame{position:absolute;left:283px;top:189px;width:634px;height:127px;border:1.5px solid rgba(255,255,255,.85);border-top:none}
.hero-frame::before,.hero-frame::after{content:"";position:absolute;top:0;height:1.5px;background:rgba(255,255,255,.85);width:38px}
.hero-frame::before{left:0}.hero-frame::after{right:0}
.hero h1{position:absolute;left:0;width:1200px;top:168px;text-align:center;font-size:39px;font-weight:700;color:var(--white);letter-spacing:.3px}
.hero p{position:absolute;left:0;width:1200px;top:224px;text-align:center;font-size:16.5px;line-height:26px;color:var(--white)}
.btn{display:inline-flex;align-items:center;justify-content:center;gap:8px;background:var(--blue);color:var(--white);font-size:13.5px;text-decoration:none}
.hero .btn{position:absolute;left:527px;top:296px;width:147px;height:38px;border:1.5px solid var(--white)}
.dots{position:absolute;left:0;width:1200px;display:flex;justify-content:center;gap:6px}
.dots span{width:8px;height:8px;border:1px solid var(--white)}
.dots span.on{background:var(--white)}
.dots.blue span{border-color:var(--blue)}
.dots.blue span.on{background:var(--blue)}

/* section titles */
.title{position:absolute;left:0;width:1200px;text-align:center;font-size:33px;font-weight:500}
.rule{position:absolute;height:2px;width:44px;background:var(--blue)}

/* about */
.about-frame{position:absolute;left:141px;top:671px;width:438px;height:402px;border:1.5px solid var(--blue)}
.about-photo{position:absolute;left:162px;top:692px;width:438px;height:359px;background:linear-gradient(135deg,#dfe7ee 0%,#b9c9d6 45%,#8fa7b8 75%,#5c7e6a 100%)}
.about-copy{position:absolute;left:684px;top:680px;width:376px}
.about-copy h2{font-size:32px;font-weight:500}
.about-copy .rule{position:static;margin:8px 0 16px}
.about-copy h3{font-size:15.5px;font-weight:600;margin-bottom:8px}
.about-copy p{font-size:12.5px;line-height:19px;color:var(--muted)}
.feature{display:flex;gap:20px;margin-top:26px}
.feature-icon{flex:none;width:53px;height:53px;border:1.5px solid var(--blue);display:flex;align-items:center;justify-content:center}
.feature h4{font-size:15px;font-weight:500;margin-bottom:5px}
.feature p{font-size:12px;line-height:16px}
.more{display:inline-flex;align-items:center;gap:6px;color:var(--blue);font-size:13.5px;margin-top:22px;text-decoration:none}

/* services */
.services-band{position:absolute;left:0;top:1143px;width:1200px;height:305px;background:linear-gradient(180deg,#0d57b6,#0a4ca3)}
.services-sub{position:absolute;left:0;width:1200px;top:1276px;text-align:center;font-size:14.5px;font-weight:500;color:var(--white)}
.card{position:absolute;top:1323px;height:232px;border:1.5px solid var(--blue);background:var(--white);text-align:center;padding-top:30px}
.card.featured{background:var(--blue);color:var(--white)}
.card svg{display:block;margin:0 auto}
.card h3{font-size:17px;font-weight:600;margin-top:20px}
.card p{font-size:12.5px;line-height:16.5px;color:var(--muted);margin:9px auto 0;width:175px}
.card.featured p{color:var(--white)}
.plus{position:absolute;left:50%;bottom:-12px;margin-left:-11px;width:22px;height:22px;background:var(--white);border:1.5px solid var(--blue);color:var(--blue);font-size:18px;line-height:18px;text-align:center}

/* why choose */
.why{position:absolute;left:0;top:1640px;width:1200px;height:502px;background:linear-gradient(120deg,#eef1f5 0%,#f7f8fa 45%,#eef2f6 75%,#f2ece6 100%)}
.why-icon{position:absolute;width:70px;height:70px;border:1.5px solid var(--blue);background:var(--white);display:flex;align-items:center;justify-content:center}
.why-icon.filled{background:var(--blue)}
.why-label{position:absolute;font-size:14.5px;color:var(--ink);white-space:nowrap}
.why-label.left{text-align:right;width:240px;left:58px}
.center-card{position:absolute;left:494px;top:1839px;width:212px;height:183px;background:var(--white);box-shadow:0 4px 20px rgba(0,0,0,.06);display:flex;align-items:center;justify-content:center}
.center-card .brand{font-size:25px}

/* reviews */
.review-quote{position:absolute;left:0;width:1200px;top:2282px;text-align:center;font-size:90px;line-height:90px;color:#a9c9f3;font-weight:700;height:50px;overflow:hidden}
.review-text{position:absolute;left:300px;width:600px;top:2336px;text-align:center;font-size:14px;line-height:22.5px;font-style:italic;color:var(--muted)}
.review-name{position:absolute;left:0;width:1200px;top:2416px;text-align:center;font-size:14.5px;font-weight:600}
.arrow-box{position:absolute;width:31px;height:31px;border:1.5px solid var(--blue);display:flex;align-items:center;justify-content:center;background:transparent}
.arrow-box.grey{border-color:#b7bcc3}

/* partners */
.partners{position:absolute;left:0;top:2540px;width:1200px;height:317px;background:var(--panel)}
.partner{position:absolute;top:2689px;height:98px;background:var(--white);border:1px solid #e3e5e8;box-shadow:0 2px 8px rgba(0,0,0,.05);display:flex;align-items:center;justify-content:center;gap:8px;font-size:21px;font-weight:600;color:#7c8189}
.partner .dot{width:12px;height:12px;border-radius:50%;background:#9aa0a8}

/* footer */
.site-footer{position:absolute;left:0;top:2857px;width:1200px;height:286px;background:var(--footer);color:#e8e9eb}
.footer-col{position:absolute;top:58px}
.footer-col h4{font-size:16.5px;font-weight:500;color:var(--white)}
.footer-col .rule{position:static;width:36px;height:2px;margin:6px 0 14px}
.quick-links li{list-style:none;font-size:11.5px;height:25px;display:flex;align-items:center;gap:8px}
.quick-links li::before{content:"";width:4px;height:4px;border:1px solid #8a8e95}
.contact-row{display:flex;gap:12px;font-size:11.5px;line-height:15px;margin-bottom:14px}
.contact-row svg{flex:none;margin-top:1px}
.footer-col p.note{font-size:11px;line-height:17px;width:210px}
.email-field{margin-top:12px;width:212px;height:31px;border:1px solid #6b6f76;font-size:11px;color:#9ca0a7;padding:9px 10px}
.site-footer .btn{margin-top:12px;width:106px;height:30px;font-size:12px}
.footer-brand{position:absolute;left:921px;top:53px;width:94px;height:92px;display:flex;align-items:center;justify-content:center}
.footer-brand .brand{font-size:19px;color:var(--white);gap:7px}
.footer-brand .brand-square{width:10px;height:10px}
.social{position:absolute;top:176px;width:33px;height:31px;border:1.5px solid #c9ccd1}
.social.on{background:var(--blue);border-color:var(--white)}
.footer-bar{position:absolute;left:0;bottom:0;width:1200px;height:45px;background:var(--footer-bar);text-align:center;font-size:11px;line-height:45px;color:#d6d8db}
</style>
</head>
<body>
<div class="page">

<header class="site-header">
  <div class="brand"><span class="brand-square"></span>Verantel Dx</div>
  <div class="contact-chip" style="left:728px">
    <span class="chip-icon"><svg width="14" height="14" viewBox="0 0 24 24"><path d="M6.6 10.8a15 15 0 0 0 6.6 6.6l2.2-2.2a1 1 0 0 1 1-.25 11 11 0 0 0 3.6.6 1 1 0 0 1 1 1V20a1 1 0 0 1-1 1A17 17 0 0 1 3 4a1 1 0 0 1 1-1h3.5a1 1 0 0 1 1 1 11 11 0 0 0 .6 3.6 1 1 0 0 1-.25 1z" fill="#1a80ec"/></svg></span>
    <span style="font-size:18.5px;font-weight:500">215 555 0148</span>
  </div>
  <div class="contact-chip" style="left:896px">
    <span class="chip-icon"><svg width="14" height="11" viewBox="0 0 24 18"><path d="M0 0h24v2l-12 8L0 2z M0 5l12 8 12-8v13H0z" fill="#1a80ec"/></svg></span>
    <span style="font-size:14px">info@verantelmail.com</span>
  </div>
  <nav class="nav">
    <a class="active" href="#" style="left:522px">Home</a>
    <a href="#" style="left:621px">About Us</a>
    <a href="#" style="left:741px">Services</a>
    <a href="#" style="left:856px">Resources</a>
    <a href="#" style="left:984px">Contact Us</a>
  </nav>
</header>

<section class="hero" role="img" aria-label="Background photograph of blue magnified cells and a DNA strand">
  <div class="hero-frame"></div>
  <h1>BIOTECH CONSULTING FIRM</h1>
  <p>We Serve Medical Diagnostics Industry, Which Is Part Of The<br>Life Science/healthcare Industry.</p>
  <a class="btn" href="#">READ MORE <svg width="18" height="8" viewBox="0 0 18 8"><path d="M0 4h16M13 1l3 3-3 3" stroke="#fff" fill="none"/></svg></a>
  <div class="dots" style="top:451px"><span class="on"></span><span></span><span></span><span></span></div>
</section>

<section class="about">
  <div class="about-frame"></div>
  <div class="about-photo" role="img" aria-label="Photograph of a scientist with a pipette and tweezers examining a plant seedling"></div>
  <div class="about-copy">
    <h2>About <span class="accent">Us</span></h2>
    <div class="rule"></div>
    <h3>Duis autem vel eum iriure dolor in hendrerit.</h3>
    <p>Lorem ipsum dolor sit amet, consectetuer adipiscing elit, sedmk diam nonummy nibh euismod tincidunt ut laoreet dolore magna aliquam erat volutpat. Suscipit lobortis nisl ut aliquip ex eamo kl commodo consequat.</p>
    <div class="feature">
      <span class="feature-icon"><svg width="28" height="28" viewBox="0 0 28 28" fill="none" stroke="#555b63" stroke-width="1.3"><circle cx="13" cy="15" r="11"/><circle cx="13" cy="15" r="6.5"/><circle cx="13" cy="15" r="2"/><path d="M13 15 24 4M20 4h4v4"/></svg></span>
      <div><h4>Mission</h4><p>Accumsan et iusto odio dignissim qui blandit dollarl praesent luptatum zzril delenit augue.</p></div>
    </div>
    <div class="feature">
      <span class="feature-icon"><svg width="30" height="20" viewBox="0 0 30 20" fill="none" stroke="#555b63" stroke-width="1.3"><path d="M1 10C6 2 24 2 29 10 24 18 6 18 1 10z"/><circle cx="15" cy="10" r="5"/><circle cx="15" cy="10" r="2"/></svg></span>
      <div><h4>Vision</h4><p>Accumsan et iusto odio dignissim qui blandit dollarl praesent luptatum zzril delenit augue.</p></div>
    </div>
    <a class="more" href="#">READ MORE <svg width="18" height="8" viewBox="0 0 18 8"><path d="M0 4h16M13 1l3 3-3 3" stroke="#1a80ec" fill="none"/></svg></a>
  </div>
</section>

<section class="services">
  <div class="services-band" role="img" aria-label="Deep blue band with a faint DNA strand image"></div>
  <h2 class="title" style="top:1205px;color:#fff">Our Services</h2>
  <div class="rule" style="left:578px;top:1254px;background:#fff"></div>
  <p class="services-sub">Lorem ipsum dolor sit amet, consectetuer adipiscing elit, sedmk diam nonummy nibh euismod.</p>

  <article class="card featured" style="left:141px;width:219px">
    <svg width="58" height="54" viewBox="0 0 58 54" fill="none" stroke="#fff" stroke-width="1.6"><circle cx="20" cy="24" r="13"/><path d="M10 33 2 48"/><circle cx="40" cy="26" r="14"/><path d="M40 18v8l6 4M36 8h8M40 8v4"/></svg>
    <h3>Corporate Strategy</h3>
    <p>Lorem ipsum dolor sit amet, consectetuer adipiscing elit, sedmk diam nonummy.</p>
    <span class="plus">+</span>
  </article>
  <article class="card" style="left:378px;width:215px">
    <svg width="58" height="54" viewBox="0 0 58 54" fill="none" stroke="#1a80ec" stroke-width="1.6"><path d="M8 26 29 16l21 10-21 10z M8 26v16l21 10 21-10V26 M29 36v16"/><circle cx="29" cy="12" r="6"/><path d="M29 1v3M19 6l2 2M39 6l-2 2"/></svg>
    <h3>Product Development</h3>
    <p>Lorem ipsum dolor sit amet, consectetuer adipiscing elit, sedmk diam nonummy.</p>
    <span class="plus">+</span>
  </article>
  <article class="card" style="left:611px;width:215px">
    <svg width="58" height="58" viewBox="0 0 58 58" fill="none" stroke="#1a80ec" stroke-width="1.6"><path d="M8 4h30l10 10v40H8z M38 4v10h10"/><circle cx="22" cy="30" r="8"/><circle cx="22" cy="30" r="3"/><circle cx="38" cy="32" r="5"/><path d="M14 46h28"/></svg>
    <h3>Business Development</h3>
    <p>Lorem ipsum dolor sit amet, consectetuer adipiscing elit, sedmk diam nonummy.</p>
    <span class="plus">+</span>
  </article>
  <article class="card" style="left:844px;width:215px">
    <svg width="58" height="54" viewBox="0 0 58 54" fill="none" stroke="#1a80ec" stroke-width="1.6"><path d="M6 4h46l4 14H2z M6 18v32h46V18 M14 50V30h10v20 M32 28h14v14H32z M39 31v8M35 35h8"/></svg>
    <h3>Commercialization</h3>
    <p>Lorem ipsum dolor sit amet, consectetuer adipiscing elit, sedmk diam nonummy.</p>
    <span class="plus">+</span>
  </article>
</section>

<section class="why-section">
  <div class="why" role="img" aria-label="Faint pale photograph of a laboratory desk with medical items"></div>
  <h2 class="title" style="top:1696px">Why Choose <span class="accent">Us?</span></h2>
  <div class="rule" style="left:578px;top:1745px"></div>

  <svg class="abs" style="left:0;top:0" width="1200" height="3143" fill="none" stroke="#aebfd3" stroke-width="1">
    <path d="M382 1825H440L494 1880M382 1930H494M382 2036H440L494 1985"/>
    <path d="M818 1825H760L706 1880M818 1930H706M818 2036H760L706 1985"/>
  </svg>

  <div class="center-card"><div class="brand"><span class="brand-square"></span>Verantel Dx</div></div>

  <span class="why-label left" style="top:1815px">Years Of Experience</span>
  <span class="why-label left" style="top:1921px">Proffesional Team</span>
  <span class="why-label left" style="top:2027px">Best Valuation</span>
  <div class="why-icon filled" style="left:312px;top:1789px"><svg width="36" height="42" viewBox="0 0 36 42" fill="none" stroke="#fff" stroke-width="1.6"><circle cx="18" cy="16" r="13"/><circle cx="18" cy="16" r="8"/><path d="M14 16l3 3 5-6M10 27 6 40l6-3 3 4 3-11M26 27l4 13-6-3-3 4-3-11"/></svg></div>
  <div class="why-icon" style="left:312px;top:1895px"><svg width="44" height="38" viewBox="0 0 44 38" fill="none" stroke="#555b63" stroke-width="1.4"><circle cx="22" cy="12" r="7"/><path d="M10 36c0-8 5-13 12-13s12 5 12 13"/><circle cx="8" cy="14" r="5"/><circle cx="36" cy="14" r="5"/><path d="M1 32c0-6 3-10 7-10M43 32c0-6-3-10-7-10"/></svg></div>
  <div class="why-icon" style="left:312px;top:2001px"><svg width="40" height="40" viewBox="0 0 40 40" fill="none" stroke="#555b63" stroke-width="1.4"><path d="M10 4h20l6 8-16 14L4 12z M4 12h32 M20 26 14 12l6-8 6 8z M8 26v10h24V26"/></svg></div>

  <div class="why-icon" style="left:818px;top:1789px"><svg width="38" height="40" viewBox="0 0 38 40" fill="none" stroke="#555b63" stroke-width="1.4"><path d="M18 4l6 3-8 16-6-3z M14 22l-2 6M20 16a10 10 0 0 1 6 16 M4 36h30 M8 32h20"/></svg></div>
  <div class="why-icon" style="left:818px;top:1895px"><svg width="42" height="42" viewBox="0 0 42 42" fill="none" stroke="#555b63" stroke-width="1.4"><circle cx="21" cy="21" r="19"/><circle cx="21" cy="21" r="15"/><path d="M21 10v11l7 5"/></svg></div>
  <div class="why-icon" style="left:818px;top:2001px"><svg width="40" height="40" viewBox="0 0 40 40" fill="none" stroke="#555b63" stroke-width="1.4"><circle cx="20" cy="14" r="8"/><path d="M10 14a10 10 0 0 1 20 0M9 13h3v6H9zM28 13h3v6h-3zM30 19c0 3-3 5-7 5 M4 38c0-9 7-13 16-13s16 4 16 13"/></svg></div>
  <span class="why-label" style="left:900px;top:1815px">Innovative Research</span>
  <span class="why-label" style="left:900px;top:1921px">On Time Solutions</span>
  <span class="why-label" style="left:900px;top:2027px">Start-up Support</span>
</section>

<section class="reviews">
  <h2 class="title" style="top:2198px">Customer <span class="accent">Reviews</span></h2>
  <div class="rule" style="left:578px;top:2247px"></div>
  <div class="review-quote">&ldquo;</div>
  <p class="review-text">"Lorem ipsum dolor sit amet, consectetuer adipiscing elit, sedmk diam nonummy nibh euismod tincidunt ut laoreet dolore magna aliquam erat volutpat. Suscipit lobortis nisl ut aliquip ex eamo kl commodo consequat."</p>
  <p class="review-name">-Mr. Aren Kalloway</p>
  <div class="dots blue" style="top:2461px"><span class="on"></span><span></span><span></span><span></span></div>
  <span class="arrow-box grey" style="left:141px;top:2372px"><svg width="10" height="16" viewBox="0 0 10 16"><path d="M8 1 2 8l6 7" stroke="#9aa0a8" fill="none" stroke-width="1.3"/></svg></span>
  <span class="arrow-box" style="left:1028px;top:2372px"><svg width="10" height="16" viewBox="0 0 10 16"><path d="M2 1l6 7-6 7" stroke="#1a80ec" fill="none" stroke-width="1.3"/></svg></span>
</section>

<section class="partners-section">
  <div class="partners"></div>
  <h2 class="title" style="top:2602px">Our <span class="accent">Parteners</span></h2>
  <div class="rule" style="left:578px;top:2651px"></div>
  <span class="arrow-box grey" style="left:71px;top:2723px"><svg width="10" height="16" viewBox="0 0 10 16"><path d="M8 1 2 8l6 7" stroke="#9aa0a8" fill="none" stroke-width="1.3"/></svg></span>
  <div class="partner" style="left:141px;width:169px"><span class="dot"></span>Timberly</div>
  <div class="partner" style="left:329px;width:169px">Quarrow</div>
  <div class="partner" style="left:516px;width:168px">Fernlake</div>
  <div class="partner" style="left:704px;width:167px">Millstack</div>
  <div class="partner" style="left:890px;width:169px">Bolderon</div>
  <span class="arrow-box" style="left:1099px;top:2723px"><svg width="10" height="16" viewBox="0 0 10 16"><path d="M2 1l6 7-6 7" stroke="#1a80ec" fill="none" stroke-width="1.3"/></svg></span>
</section>

<footer class="site-footer">
  <div class="footer-col" style="left:141px">
    <h4>Quick <span class="accent">Links</span></h4>
    <div class="rule"></div>
    <ul class="quick-links"><li>Home</li><li>About Us</li><li>Services</li><li>Resources</li><li>Contact Us</li></ul>
  </div>
  <div class="footer-col" style="left:332px">
    <h4>Contact <span class="accent">Detail</span></h4>
    <div class="rule"></div>
    <div class="contact-row"><svg width="12" height="15" viewBox="0 0 12 15" fill="none" stroke="#cfd2d6"><path d="M6 14C2 9 1 7 1 5.5a5 5 0 0 1 10 0C11 7 10 9 6 14z"/><circle cx="6" cy="5.5" r="1.8"/></svg><div><b style="font-weight:600">Verantel Dx</b><br><span style="display:block;margin-top:4px">48 Corvane Street,<br>Halbrook, PA-19 104</span></div></div>
    <div class="contact-row" style="font-size:13.5px"><svg width="14" height="14" viewBox="0 0 24 24" fill="none" stroke="#cfd2d6" stroke-width="1.6"><path d="M6.6 10.8a15 15 0 0 0 6.6 6.6l2.2-2.2 4.6 1V20a1 1 0 0 1-1 1A17 17 0 0 1 3 4a1 1 0 0 1 1-1h3.5l1 4.6z"/></svg>215 555 0148</div>
    <div class="contact-row"><svg width="14" height="11" viewBox="0 0 14 11" fill="none" stroke="#cfd2d6"><rect x=".5" y=".5" width="13" height="10"/><path d="M.5.5 7 6l6.5-5.5"/></svg>info@verantelmail.com</div>
  </div>
  <div class="footer-col" style="left:593px">
    <h4>Newsletter <span class="accent">Signup</span></h4>
    <div class="rule"></div>
    <p class="note">Lorem ipsum dolor sit amet, consectetu adipiscing elit, sedmk nonummy.</p>
    <div class="email-field">Email</div>
    <a class="btn" href="#">SUBMIT <svg width="16" height="8" viewBox="0 0 18 8"><path d="M0 4h16M13 1l3 3-3 3" stroke="#fff" fill="none"/></svg></a>
  </div>
  <div class="footer-brand"><div class="brand"><span class="brand-square"></span>Verantel Dx</div></div>
  <span class="social on" style="left:900px"></span>
  <span class="social" style="left:943px"></span>
  <span class="social" style="left:985px"></span>
  <span class="social" style="left:1028px"></span>
  <div class="footer-bar">Copyright &nbsp;2019 - Verantel Dx. All Rights Reserved.</div>
</footer>

</div>
</body>
</html>
```